Business Card - connecting 2 souls and beggining the journey of self discovery

Logo on the front
with tag line

On the back list of services and contact details

Seminars
workshops
Coaching
podcasts

Darren Whitlow
Health & Wellbeing Life Coach
0491 372 615
darren@brightcoreliving.example
brightcoreliving.example

Industry/Entity Type

Life Coaching

Contact Information for Business Card

I like the use of colour from the logo to be used. I'm not a fan of white.

Requirements
Must have
• My tagline: The journey home starts with you
Nice to have
• Use of colour that is in the mind body soul logo

```html
<!DOCTYPE html>
<html lang="en">
<head>
<meta charset="utf-8">
<title>Brightcore Living — Business Card</title>
<link rel="stylesheet" href="https://fonts.googleapis.com/css2?family=Montserrat:wght@400;500&family=Open+Sans:wght@400;600;700&display=swap">
<style>
  :root {
    --purple: #7b3f9e;
    --purple-light: #8a52ad;
    --ink: #444444;
    --ink-soft: #555555;
    --card-white: #ffffff;
    --backdrop: #e6e6e8;
  }
  * { box-sizing: border-box; margin: 0; padding: 0; }
  html, body {
    width: 1200px; height: 1000px; overflow: hidden;
    background: var(--backdrop);
  }
  .stage {
    position: relative; width: 1200px; height: 1000px;
  }
  .card {
    position: absolute; left: 250px; width: 700px; height: 400px;
    border-radius: 22px; overflow: hidden;
    box-shadow: 0 8px 24px rgba(0,0,0,0.15);
  }

  /* Front */
  .card-front { top: 60px; background: var(--purple); color: #fff; }
  .front-brand {
    position: absolute; top: 130px; width: 100%; text-align: center;
    font-family: "Montserrat", sans-serif; font-weight: 500;
    font-size: 52px; letter-spacing: -2.5px;
  }
  .front-pillars {
    position: absolute; top: 205px; width: 100%; text-align: center;
    font-family: "Montserrat", sans-serif; font-size: 11px; letter-spacing: 4px;
  }
  .front-tagline {
    position: absolute; top: 320px; width: 100%; text-align: center;
    font-family: "Montserrat", sans-serif; font-size: 13px; letter-spacing: 4.5px;
  }

  /* Back */
  .card-back { top: 540px; background: var(--card-white); }
  .side-band {
    position: absolute; left: 20px; top: 0; width: 50px; height: 100%;
    background: var(--purple-light);
  }
  .brand-lockup {
    position: absolute; right: 50px; top: 48px; text-align: right;
  }
  .brand-dot {
    display: block; margin: 0 0 12px auto; width: 62px; height: 62px;
    border-radius: 50%; background: var(--purple);
  }
  .brand-name {
    font-family: "Montserrat", sans-serif; font-weight: 500;
    font-size: 27px; letter-spacing: -1.3px; color: var(--ink-soft);
  }
  .person { position: absolute; left: 110px; top: 118px; font-family: "Open Sans", sans-serif; }
  .person-name { font-weight: 700; font-size: 30px; color: var(--ink); letter-spacing: 0.5px; line-height: 1.1; }
  .person-role { font-weight: 600; font-size: 19px; color: var(--purple); }
  .divider {
    position: absolute; left: 110px; top: 190px; width: 520px; height: 2px;
    background: var(--purple);
  }
  .contacts {
    position: absolute; left: 110px; top: 208px; list-style: none;
    font-family: "Open Sans", sans-serif; font-size: 17px; color: var(--ink);
  }
  .contacts li { display: flex; align-items: center; gap: 10px; line-height: 27px; }
  .contacts svg { width: 16px; height: 16px; flex: none; }
  .web-accent { color: var(--purple); }
  .services {
    position: absolute; right: 80px; top: 300px; text-align: right;
    font-family: "Open Sans", sans-serif; font-size: 20px; color: var(--ink);
    line-height: 27px;
  }
</style>
</head>
<body>
<main class="stage">
  <section class="card card-front">
    <h1 class="front-brand">Brightcore Living</h1>
    <p class="front-pillars">MIND | BODY | SOUL</p>
    <p class="front-tagline">THE JOURNEY HOME STARTS WITH YOU</p>
  </section>

  <section class="card card-back">
    <div class="side-band"></div>

    <div class="brand-lockup">
      <span class="brand-dot"></span>
      <p class="brand-name">Brightcore Living</p>
    </div>

    <div class="person">
      <h2 class="person-name">DARREN WHITLOW</h2>
      <p class="person-role">Life Coach</p>
    </div>
    <div class="divider"></div>

    <ul class="contacts">
      <li>
        <svg viewBox="0 0 16 16" aria-hidden="true"><rect x="4" y="1" width="8" height="14" rx="1.5" fill="none" stroke="var(--purple)" stroke-width="1.5"/><circle cx="8" cy="12.5" r="0.9" fill="var(--purple)"/></svg>
        0491 372 615
      </li>
      <li>
        <svg viewBox="0 0 16 16" aria-hidden="true"><rect x="1" y="3" width="14" height="10" rx="1" fill="var(--purple)"/><path d="M1.5 3.5 L8 9 L14.5 3.5" fill="none" stroke="#fff" stroke-width="1.2"/></svg>
        darren@brightcoreliving.example
      </li>
      <li>
        <svg viewBox="0 0 16 16" aria-hidden="true"><circle cx="8" cy="8" r="7" fill="var(--purple)"/><path d="M1 8 H15 M8 1 C4 5 4 11 8 15 M8 1 C12 5 12 11 8 15" fill="none" stroke="#fff" stroke-width="1"/></svg>
        <span>www.<span class="web-accent">brightcoreliving</span>.example</span>
      </li>
    </ul>

    <div class="services">
      <p>Seminars | Workshops</p>
      <p>Coaching | Podcasts</p>
    </div>
  </section>
</main>
</body>
</html>
```